Real Estate Newsletter

I would like a template created for a monthly newsletter; ideally, two pages long, including my photo, logo and contact info. I need it to look professional and be very easy for me to drop text into.

Target Market(s)

Past/current clients

Industry/Entity Type

Real Estate Agent

Font styles to use
Serif

Requirements
Must have
• My contact info/photo and logo
• (206) 555-0173
• mkorvell@tlxhb.com
• www.MarenKorvell.com
Nice to have
• I need a template where I can easily drop contact. I need the template to look professional so I can print it and mail it to current and past clients.

```html
<!DOCTYPE html>
<html lang="en">
<head>
<meta charset="utf-8">
<title>Maren Korvell – Newsletter</title>
<link href="https://fonts.googleapis.com/css2?family=Libre+Baskerville:wght@400;700&display=swap" rel="stylesheet">
<style>
  :root {
    --frame: #d5d6da;
    --paper: #ffffff;
    --band: #c8cbe6;
    --navy: #2b3a9a;
    --ink: #1a1a1a;
    --ring: #8a93cc;
  }
  * { margin: 0; padding: 0; box-sizing: border-box; }
  html, body { width: 1200px; height: 1200px; overflow: hidden; background: #ffffff; }
  .canvas { position: relative; width: 1200px; height: 1200px; font-family: "Libre Baskerville", Georgia, serif; }
  .frame { position: absolute; left: 56px; top: 50px; width: 1103px; height: 1102px; background: var(--frame); }
  .page { position: absolute; left: 77px; top: 76px; width: 1057px; height: 1056px; background: var(--paper); }
  .abs { position: absolute; }
  .header-band { position: absolute; left: 158px; top: 76px; }
  .brand-name { left: 158px; width: 900px; top: 160px; text-align: center; font-size: 40px; font-weight: 700; color: var(--navy); letter-spacing: 0.02em; white-space: nowrap; }
  .portrait { left: 269px; top: 304px; width: 140px; height: 140px; border-radius: 50%; border: 4px solid var(--ring);
    background: radial-gradient(circle at 50% 45%, #c9a58c 0%, #7a5a44 45%, #e9e6e4 80%); }
  .dash-h { position: absolute; left: 172px; width: 254px; border-top: 2px dashed var(--navy); }
  .side-label { right: 774px; font-size: 19px; letter-spacing: 0.1em; color: var(--navy); text-align: right; }
  .side-text { right: 774px; font-size: 14.5px; letter-spacing: 0.06em; color: var(--navy); text-align: right; white-space: nowrap; }
  .icon { position: absolute; width: 18px; height: 18px; }
  .divider-v { left: 505px; top: 302px; height: 768px; border-left: 2px dashed var(--navy); }
  .section-title { font-size: 22px; font-weight: 400; letter-spacing: 0.06em; color: var(--navy); text-align: center; }
  .rule { position: absolute; border-top: 1.5px dashed var(--navy); }
  .body-copy { font-size: 14px; line-height: 18px; letter-spacing: 0.1em; color: var(--ink); text-align: justify; }
  .body-copy p + p { margin-top: 18px; }
  .field { left: 174px; width: 252px; font-size: 14.5px; letter-spacing: 0.06em; color: var(--navy); display: flex; white-space: nowrap; }
  .field .label { width: 118px; }
  .field .fill { flex: 1; overflow: hidden; }
</style>
</head>
<body>
<div class="canvas">
  <div class="frame"></div>
  <div class="page"></div>

  <svg class="header-band" width="900" height="192" viewBox="0 0 900 192" aria-hidden="true">
    <polygon points="0,0 900,0 900,160 450,190 0,160" fill="var(--band)"/>
  </svg>
  <div class="abs brand-name">Maren Korvell</div>

  <div class="abs portrait" role="img" aria-label="Portrait photo of the agent"></div>

  <div class="dash-h" style="top:475px"></div>
  <div class="abs side-label" style="top:479px">CONTACT</div>
  <div class="dash-h" style="top:508px"></div>

  <svg class="icon" style="left:406px;top:523px" viewBox="0 0 18 18" aria-hidden="true">
    <circle cx="9" cy="9" r="9" fill="#111"/>
    <path d="M5.5 4.5c.6-.4 1.2-.3 1.5.2l1 1.6c.3.5.2 1-.2 1.3l-.6.5c.5 1.2 1.4 2.1 2.6 2.6l.5-.6c.3-.4.8-.5 1.3-.2l1.6 1c.5.3.6.9.2 1.5-.7 1-1.8 1.4-3 .9-2.3-1-4.1-2.8-5.1-5.1-.5-1.2-.1-2.3.2-3.7z" fill="#fff"/>
  </svg>
  <div class="abs side-text" style="top:545px">(206) 555-0173</div>

  <svg class="icon" style="left:407px;top:583px" viewBox="0 0 18 18" aria-hidden="true">
    <circle cx="9" cy="9" r="9" fill="#111"/>
    <rect x="4" y="5.5" width="10" height="7" fill="#fff"/>
    <path d="M4 5.5l5 4 5-4" fill="none" stroke="#111" stroke-width="1"/>
  </svg>
  <div class="abs side-text" style="top:600px">mkorvell@tlxhb.com</div>

  <svg class="icon" style="left:407px;top:639px" viewBox="0 0 18 18" aria-hidden="true">
    <circle cx="9" cy="9" r="7.5" fill="none" stroke="#111" stroke-width="1.6"/>
    <ellipse cx="9" cy="9" rx="3.2" ry="7.5" fill="none" stroke="#111" stroke-width="1.3"/>
    <line x1="1.5" y1="9" x2="16.5" y2="9" stroke="#111" stroke-width="1.3"/>
    <line x1="3" y1="5.5" x2="15" y2="5.5" stroke="#111" stroke-width="1.1"/>
    <line x1="3" y1="12.5" x2="15" y2="12.5" stroke="#111" stroke-width="1.1"/>
  </svg>
  <div class="abs side-text" style="top:657px">www.MarenKorvell.com</div>

  <div class="dash-h" style="top:730px"></div>
  <div class="abs side-label" style="top:739px">DATE</div>
  <div class="dash-h" style="top:768px"></div>
  <div class="abs side-text" style="top:785px">[example] 12<sup style="font-size:8px">th</sup> February 2018</div>

  <div class="dash-h" style="top:861px"></div>
  <div class="abs side-label" style="top:866px">CONTACT</div>
  <div class="dash-h" style="top:895px"></div>

  <div class="abs field" style="top:913px"><span class="label">Client Name</span><span class="fill">: ......................................</span></div>
  <div class="abs field" style="top:949px"><span class="label">Phone</span><span class="fill">: ......................................</span></div>
  <div class="abs field" style="top:985px"><span class="label">Email</span><span class="fill">: ......................................</span></div>
  <div class="abs field" style="top:1021px"><span class="label">Address</span><span class="fill">: ......................................</span></div>

  <div class="abs divider-v"></div>

  <h2 class="abs section-title" style="left:579px;width:485px;top:318px">The Real Estate Market</h2>
  <div class="rule" style="left:579px;width:485px;top:359px"></div>
  <div class="abs body-copy" style="left:579px;width:485px;top:376px">
    <p>Many buyers and sellers are left feeling overwhelmed with the process and where to even begin. My job is to explain and guide you through the entire real estate process, from the initial meeting through the closing. I will be available day in and out to answer any questions you may have and address any concerns. My goal is that you feel you have my undivided attention during this process. I've spent my entire life in Seattle- born and raised in the Greenlake area- and I currently reside in Shoreline, after recently relocating from Lake Forest Park. On the side, my husband and I rehab and manage our rental properties. This side hobby has given me a unique perspective on handling renovations, local rents, and the potential appreciation of properties.</p>
    <p>I love what I do and the people I get to work with. I would be honored to walk through this process with you.</p>
  </div>

  <h2 class="abs section-title" style="left:579px;width:485px;top:778px">Information</h2>
  <div class="rule" style="left:579px;width:485px;top:816px"></div>
  <div class="abs body-copy" style="left:570px;width:494px;top:839px">
    <p>We're all familiar with the Vistimate, available on Homevista, but did you know that the algorithm used to generate your Vistimate can't actually take into account your home's updates, condition, street conditions or curb appeal? The only way to truly find out what your home is worth is to have a quick market analysis done. With just a few answers below, I can send you a quick market analysis that will give you a general idea of what your home would sell for in today's market.</p>
  </div>
</div>
</body>
</html>
```